Heron Loan Partners Business Card

We need a business card design for our mortgage servicing company. In addition to servicing the loans of homeowners, we help homeowners with purchasing their homes and any mortgage refinancing. We would like to see designs that use the colors in the logo attached below (gold-ish yellow and navy blue), and any other design you deem fit! The design should communicate a simpler life with smart mortgages provided by Heron.

```html
<!DOCTYPE html>
<html lang="en">
<head>
<meta charset="utf-8">
<title>Heron Loan Partners Business Card</title>
<link rel="stylesheet" href="https://fonts.googleapis.com/css2?family=Arimo:wght@400;700&display=swap">
<style>
  :root {
    --gold: #d8aa35;
    --gold-text: #d4a52c;
    --navy: #24205c;
    --ink: #2b2b2b;
    --paper: #ffffff;
    --backdrop: #e6e6e8;
    --rule: #9a9a9a;
  }
  html, body {
    margin: 0;
    padding: 0;
    width: 1200px;
    height: 779px;
    overflow: hidden;
    background: var(--backdrop);
    font-family: "Arimo", Arial, sans-serif;
  }
  .canvas {
    position: relative;
    width: 1200px;
    height: 779px;
  }
  .card {
    position: absolute;
    top: 235px;
    width: 540px;
    height: 309px;
    box-shadow: 0 6px 18px rgba(0,0,0,0.18);
    box-sizing: border-box;
  }
  .card--front {
    left: 40px;
    background: var(--gold);
  }
  .card--back {
    left: 620px;
    background: var(--paper);
    border-bottom: 3px solid var(--navy);
  }
  .brand {
    display: flex;
    align-items: center;
    gap: 10px;
    color: var(--navy);
    font-weight: 700;
    white-space: nowrap;
  }
  .brand__dot {
    width: 14px;
    height: 14px;
    border-radius: 50%;
    background: var(--navy);
    flex: none;
  }
  .card--front .brand {
    position: absolute;
    left: 0;
    right: 0;
    top: 108px;
    justify-content: center;
    font-size: 38px;
  }
  .card--front .website {
    position: absolute;
    left: 0;
    right: 0;
    top: 206px;
    text-align: center;
    font-size: 13px;
    letter-spacing: 3px;
    color: var(--navy);
  }
  .card--back .brand {
    position: absolute;
    right: 28px;
    top: 30px;
    font-size: 17px;
    color: var(--gold-text);
  }
  .card--back .brand__dot {
    width: 10px;
    height: 10px;
    background: var(--navy);
  }
  .holder {
    position: absolute;
    left: 36px;
    top: 150px;
  }
  .holder__name {
    margin: 0;
    font-size: 22px;
    font-weight: 700;
    color: var(--gold-text);
  }
  .holder__title {
    margin: 2px 0 8px;
    font-size: 16px;
    color: var(--navy);
  }
  .contact {
    font-size: 15px;
    color: var(--ink);
    line-height: 1.35;
  }
  .contact__label {
    color: var(--gold-text);
    font-weight: 700;
    margin-right: 4px;
  }
  .address {
    margin: 14px 0 10px;
    font-style: normal;
    font-size: 15px;
    line-height: 1.3;
    color: var(--ink);
  }
  .tagline {
    margin: 0;
    font-size: 15px;
    color: var(--ink);
  }
  .online {
    position: absolute;
    left: 300px;
    top: 190px;
    padding-left: 16px;
    border-left: 1px solid var(--rule);
  }
</style>
</head>
<body>
<div class="canvas">
  <section class="card card--front" aria-label="Card front">
    <div class="brand"><span class="brand__dot"></span>Heron Loan Partners</div>
    <div class="website">www.Heron.com</div>
  </section>

  <section class="card card--back" aria-label="Card back">
    <div class="brand"><span class="brand__dot"></span>Heron Loan Partners</div>
    <div class="holder">
      <h1 class="holder__name">Daniel Reyes</h1>
      <div class="holder__title">President</div>
      <div class="contact"><span class="contact__label">P :</span>(555) 0142-7788</div>
      <address class="address">4127 Alder Court<br>Glenmoor, NY 11020</address>
      <p class="tagline">Simpler life with smart mortgages</p>
    </div>
    <div class="online">
      <div class="contact"><span class="contact__label">E :</span>name@Heron.com</div>
      <div class="contact"><span class="contact__label">W :</span>www.Heron.com</div>
    </div>
  </section>
</div>
</body>
</html>
```